Professional, modern and unique business card. We are looking to present a new look to our business cards however we don't want to divert too far away from original template. We want social media links and our 3 office addresses on the backside of the business cards. Please see attached business card templates for ideas.
Crestline Homes Color Code:
R: 7
G:63
B:86

Target Market(s)

Real Estate

Industry/Entity Type

Real Estate

Contact Information for Business Card

Follow the attached templates. In need of a more modern and unique touch but don't want to divert from the original theme or color.
Crestline Homes Color Code:
R: 7
G:63
B:86

Font styles to use
Serif

Requirements
Must have
• Crestline Homes logo, Crestline homes colors, social media links, 3 office addresses,
Nice to have
• information about Crestline Homes and QR codes. You can check out www.mycrestlinehomes.example

```html
<!DOCTYPE html>
<html lang="en">
<head>
<meta charset="utf-8">
<title>Crestline Homes – Business Card</title>
<link rel="stylesheet" href="https://fonts.googleapis.com/css2?family=Lora:wght@400;700&display=swap">
<style>
  :root {
    --stage: #3a3a3c;
    --brand-teal: rgb(7, 63, 86);
    --card-white: #ffffff;
    --pattern-tint: #e9f0f2;
    --text-dark: #1f2a30;
    --text-light: #ffffff;
    --divider-light: rgba(255,255,255,0.35);
    --divider-dark: #6d7a80;
    --dot-blue: #3b5998;
    --dot-red: #c4302b;
    --dot-steel: #0e76a8;
    --dot-crimson: #cb2027;
    --dot-sky: #3aa8e0;
    --dot-navy: #2d6a96;
  }
  html, body {
    margin: 0;
    padding: 0;
    width: 1200px;
    height: 782px;
    overflow: hidden;
    background: var(--stage);
    font-family: "Lora", Georgia, serif;
  }
  .canvas {
    width: 1200px;
    height: 782px;
    display: flex;
    align-items: center;
    justify-content: center;
    gap: 50px;
  }
  .card {
    position: relative;
    width: 525px;
    height: 300px;
    box-sizing: border-box;
    box-shadow: 0 6px 18px rgba(0,0,0,0.45);
    overflow: hidden;
  }

  /* Front */
  .card-front {
    background: var(--brand-teal);
    color: var(--text-light);
    display: flex;
    align-items: center;
  }
  .brand {
    width: 232px;
    box-sizing: border-box;
    padding: 0 16px 0 22px;
    display: flex;
    align-items: center;
    justify-content: center;
    gap: 9px;
  }
  .brand-dot {
    width: 12px;
    height: 12px;
    border-radius: 50%;
    background: var(--text-light);
    flex: none;
  }
  .brand-name {
    font-weight: 700;
    font-size: 22px;
    line-height: 1.15;
    color: var(--text-light);
  }
  .front-divider {
    width: 1px;
    height: 170px;
    background: var(--divider-light);
    flex: none;
  }
  .contact {
    padding-left: 22px;
  }
  .person-name {
    font-weight: 700;
    font-size: 19px;
    letter-spacing: 0.5px;
    margin: 0;
    text-transform: uppercase;
  }
  .person-title {
    font-size: 12.5px;
    letter-spacing: 0.8px;
    margin: 2px 0 12px;
    text-transform: uppercase;
  }
  .contact-list {
    list-style: none;
    margin: 0;
    padding: 0;
    font-size: 13.5px;
    line-height: 20px;
  }
  .contact-list li {
    display: flex;
    align-items: center;
    gap: 8px;
    white-space: nowrap;
  }
  .contact-list svg {
    width: 11px;
    height: 11px;
    fill: var(--text-light);
    flex: none;
  }

  /* Back */
  .card-back {
    background: var(--card-white);
    color: var(--text-dark);
    padding: 30px 28px 24px;
  }
  .back-pattern {
    position: absolute;
    inset: 0;
    background: var(--pattern-tint);
    opacity: 0.6;
  }
  .back-content {
    position: relative;
    height: 100%;
    display: flex;
    flex-direction: column;
    justify-content: space-between;
  }
  .social-block {
    display: flex;
    justify-content: space-between;
  }
  .social-list {
    list-style: none;
    margin: 0;
    padding: 0;
    font-size: 13.5px;
    line-height: 22px;
  }
  .social-list-right {
    margin-top: 58px;
  }
  .social-list li {
    display: flex;
    align-items: center;
    gap: 7px;
    white-space: nowrap;
  }
  .social-dot {
    width: 14px;
    height: 14px;
    border-radius: 50%;
    flex: none;
  }
  .dot-blue { background: var(--dot-blue); }
  .dot-red { background: var(--dot-red); }
  .dot-steel { background: var(--dot-steel); }
  .dot-crimson { background: var(--dot-crimson); }
  .dot-sky { background: var(--dot-sky); }
  .dot-navy { background: var(--dot-navy); }
  .office-list {
    display: flex;
    font-size: 12.5px;
    line-height: 17px;
  }
  .office {
    flex: 1;
    padding: 0 10px;
    border-left: 1px solid var(--divider-dark);
    font-style: normal;
    white-space: nowrap;
  }
  .office:first-child {
    padding-left: 0;
    border-left: none;
  }
</style>
</head>
<body>
<main class="canvas">
  <section class="card card-front" aria-label="Business card front">
    <div class="brand">
      <span class="brand-dot"></span>
      <span class="brand-name">Crestline Homes</span>
    </div>
    <div class="front-divider"></div>
    <div class="contact">
      <p class="person-name">Dana Whitfield</p>
      <p class="person-title">Managing Director</p>
      <ul class="contact-list">
        <li><svg viewBox="0 0 12 12"><path d="M2 1h3l1 3-1.5 1a7 7 0 0 0 2.5 2.5L8 6l3 1v3a1 1 0 0 1-1 1A9 9 0 0 1 1 2a1 1 0 0 1 1-1z"/></svg>212 555 0147</li>
        <li><svg viewBox="0 0 12 12"><path d="M3.5 0h5a1 1 0 0 1 1 1v10a1 1 0 0 1-1 1h-5a1 1 0 0 1-1-1V1a1 1 0 0 1 1-1zm.5 1.5v7.5h4V1.5z"/></svg>212 555 0198</li>
        <li><svg viewBox="0 0 12 12"><path d="M3 0h6v3H3zM1 4h10v6H9v2H3v-2H1zm3 4v3h4V8z"/></svg>212 555 0163</li>
        <li><svg viewBox="0 0 12 12"><path d="M0 2h12v8H0zm1 1v.5l5 3.5 5-3.5V3z"/></svg>info@crestline.example</li>
        <li><svg viewBox="0 0 12 12"><circle cx="6" cy="6" r="6"/></svg>www.mycrestlinehomes.example</li>
      </ul>
    </div>
  </section>

  <section class="card card-back" aria-label="Business card back">
    <div class="back-pattern" role="img" aria-label="Faint repeated brand pattern background"></div>
    <div class="back-content">
      <div class="social-block">
        <ul class="social-list">
          <li><span class="social-dot dot-blue"></span>CrestlinehomesNY</li>
          <li><span class="social-dot dot-red"></span>Info at Crestline Homes</li>
          <li><span class="social-dot dot-steel"></span>Crestline Homes New York</li>
        </ul>
        <ul class="social-list social-list-right">
          <li><span class="social-dot dot-crimson"></span>Crestline Homes</li>
          <li><span class="social-dot dot-sky"></span>@CrestlineHomesQ</li>
          <li><span class="social-dot dot-navy"></span>@CrestlineHomesNY</li>
        </ul>
      </div>
      <div class="office-list">
        <address class="office">418-07 Harbor Blvd<br>Bay Ridge, NY 11209</address>
        <address class="office">72-40 Maple Blvd<br>Forest Hill, NY 11375</address>
        <address class="office">2210 Orchard Ave<br>Brooklyn, NY 11230</address>
      </div>
    </div>
  </section>
</main>
</body>
</html>
```